UX - Need some screens design for a Skill Assessment Application

I am building an app to carry out skill assessments. Depending on how the assessment is configured, it may have one or more parts
1. Question based assessment (Multiple Choice, True False, Fill in the blanks"
2. Endorsement by two colleagues - A screen that allows user to pick colleagues based on search and shows the status of pending requests
3. A written submission - a page that explains the format of the submission and a file upload
As each assessment can be configured with or without any of the steps, the assessment UI must be such that these areas get hidden/displayed based on configuration.
Colour codes to be used can be #0e78bb and #ffffff
There will also be a start screen (instructions) and an end screen (results)
Target Market(s)
Enterprise software
Number of Pages Required
4 page

```html
<!DOCTYPE html>
<html lang="en">
<head>
<meta charset="utf-8">
<title>Skillbase – Endorsement</title>
<link href="https://fonts.googleapis.com/css2?family=Inter:wght@400;500;600;700&display=swap" rel="stylesheet">
<style>
:root{
  --brand:#0e78bb;
  --brand-dark:#1f6cae;
  --white:#ffffff;
  --ink:#1f2328;
  --muted:#5c6370;
  --line:#dfe3e8;
  --soft:#f2f3f5;
  --teal:#1d8c8c;
  --scrim:rgba(0,0,0,.42);
}
*{box-sizing:border-box;margin:0;padding:0}
html,body{width:1200px;height:771px;overflow:hidden}
body{font-family:"Inter",sans-serif;color:var(--ink);background:var(--white);position:relative;font-size:11px}
.abs{position:absolute}
.topbar{left:0;top:0;width:1200px;height:44px;background:var(--brand-dark)}
.brand-mark{left:70px;top:13px;width:18px;height:18px;border-radius:50%;background:#7fd3c8}
.brand-name{left:105px;top:13px;color:var(--white);font-size:14px;font-weight:600}
.nav{top:15px;color:#d4e4f2;font-size:12.5px}
.nav.active{color:var(--white);font-weight:700}
.nav-underline{left:487px;top:41px;width:80px;height:3px;background:#2bb3b3}
.avatar{border-radius:50%;background:linear-gradient(135deg,#a58a78,#4e3e36)}
.crumb{top:67px;font-size:11.5px;color:var(--muted)}
.crumb a{color:var(--brand);text-decoration:none}
.title{left:122px;top:98px;font-size:22px;font-weight:700}
.updated{right:90px;top:111px;font-size:11px;color:var(--muted)}
.meta{left:0;top:140px;width:1200px;height:45px;background:var(--soft);border-top:1px solid var(--line);border-bottom:1px solid var(--line)}
.meta-item{top:155px;font-size:10.5px;color:var(--ink)}
.meta-item b{font-weight:500;color:var(--brand)}
.meta-sep{top:154px;width:1px;height:16px;background:#c9cdd3}
.pill{top:151px;height:24px;border-radius:12px;background:#e2e4e8;font-size:11px;line-height:24px;padding:0 9px;color:var(--muted)}
.step{left:88px;width:214px;height:42px;border:1px solid var(--line);border-radius:4px;font-size:12px;line-height:40px;padding-left:17px;color:var(--muted)}
.step.current{border:1.5px solid var(--brand);color:var(--ink);font-weight:500}
.step.off{color:#a8adb5}
.h2{left:365px;top:219px;font-size:16px;font-weight:700}
.btn{height:31px;border:1px solid var(--brand);border-radius:3px;color:var(--brand);font-size:11.5px;font-weight:500;display:flex;align-items:center;justify-content:center;background:var(--white)}
.btn.fill{background:var(--brand);color:var(--white)}
.rule{height:1px;background:var(--line)}
.input{top:272px;height:31px;border:1px solid var(--line);border-radius:3px;font-size:11.5px;padding-left:13px;line-height:29px}
.row{left:365px;width:745px;height:59px;border:1px solid var(--line);border-radius:4px}
.chk{left:14px;top:22px;width:14px;height:14px;border:1px solid #c6cad0;border-radius:2px;background:var(--white)}
.chk.on{background:var(--brand);border-color:var(--brand)}
.row .avatar{left:37px;top:15px;width:28px;height:28px}
.row .name{left:75px;top:14px;font-size:12px;font-weight:500}
.row .role{left:75px;top:31px;font-size:10.5px;color:var(--muted)}
.row .btn{left:682px;top:13px;width:49px;height:31px}
.page{top:635px;width:31px;height:31px;font-size:13px;line-height:31px;text-align:center;color:var(--muted)}
.page.on{background:var(--brand);color:var(--white);border-radius:3px}
.pager-btn{top:635px;height:31px;border:1px solid var(--line);border-radius:3px;font-size:11px;line-height:29px;text-align:center;color:#b5bac1}
.pct{left:88px;top:662px;font-size:26px;font-weight:700}
.pct span{font-size:13px;font-weight:500}
.bar{left:0;top:702px;width:1200px;height:7px;background:#e5e7ea}
.bar i{display:block;width:750px;height:7px;background:var(--teal)}
.scrim{left:0;top:0;width:1200px;height:771px;background:var(--scrim)}
.modal{left:443px;top:246px;width:312px;height:278px;background:var(--white);border-radius:14px}
.modal h3{position:absolute;left:28px;top:28px;font-size:16px;font-weight:700}
.modal .rule{position:absolute;left:28px;top:59px;width:256px}
.modal .avatar{position:absolute;top:74px;width:27px;height:27px}
.modal p{position:absolute;left:28px;top:114px;font-size:11px;color:var(--muted);white-space:nowrap}
.modal p b{color:var(--ink)}
.modal label{position:absolute;left:28px;top:150px;font-size:9.5px;color:var(--muted)}
.select{position:absolute;left:28px;top:168px;width:257px;height:31px;border:1px solid #cfd3d8;border-radius:3px;font-size:11.5px;padding-left:13px;line-height:29px}
</style>
</head>
<body>
<header class="abs topbar">
  <div class="abs brand-mark"></div>
  <div class="abs brand-name">Skillbase</div>
  <div class="abs nav active" style="left:487px">Assessments</div>
  <div class="abs nav-underline"></div>
  <div class="abs nav" style="left:587px">Colleagues</div>
  <div class="abs nav" style="left:670px">Results</div>
  <svg class="abs" style="left:1027px;top:13px" width="18" height="18" viewBox="0 0 24 24" fill="none" stroke="#fff" stroke-width="1.6"><path d="M6 16V11a6 6 0 0 1 12 0v5l2 2H4z"/><path d="M10 20a2 2 0 0 0 4 0"/></svg>
  <svg class="abs" style="left:1062px;top:13px" width="18" height="18" viewBox="0 0 24 24" fill="none" stroke="#fff" stroke-width="1.6"><circle cx="12" cy="12" r="3"/><path d="M12 2l2 3 3.5-.8.8 3.5 3 2-2 3 .8 3.5-3.5.8-2 3-3-2-3 2-2-3-3.5-.8.8-3.5-2-3 3-2 .8-3.5 3.5.8z"/></svg>
  <div class="abs avatar" role="img" aria-label="User profile photo" style="left:1099px;top:8px;width:28px;height:28px"></div>
</header>

<svg class="abs" style="left:56px;top:65px" width="20" height="20" viewBox="0 0 20 20" fill="none" stroke="#0e78bb" stroke-width="1.6"><circle cx="10" cy="10" r="9"/><path d="M14 10H6M9 6.5L5.5 10 9 13.5"/></svg>
<div class="abs crumb" style="left:88px"><a href="#">Assessment</a> &nbsp;/&nbsp; Application Design Capabilities</div>
<svg class="abs" style="left:88px;top:101px" width="22" height="22" viewBox="0 0 22 22" fill="none" stroke="#444" stroke-width="1.4"><rect x="1" y="2" width="14" height="18" rx="1"/><path d="M4 7h8M4 11h5M4 15h4"/><circle cx="15" cy="16" r="4"/><path d="M13.5 16l1 1 2-2"/></svg>
<h1 class="abs title">Application Design Capabilities</h1>
<div class="abs updated">Last Updated: 23/05/2024</div>

<div class="abs meta"></div>
<div class="abs meta-item" style="left:88px">Assessment Date: <b>May 20, 2024</b></div>
<div class="abs meta-sep" style="left:267px"></div>
<div class="abs meta-item" style="left:288px">Assessment Type: <b>UI/UX Skill</b></div>
<div class="abs meta-sep" style="left:452px"></div>
<div class="abs meta-item" style="left:473px">Due Date: <span style="color:var(--muted)">24/05/2024</span></div>
<div class="abs pill" style="left:889px">Quiz</div>
<div class="abs pill" style="left:937px">Endorsement</div>
<div class="abs pill" style="left:1032px">Submission</div>

<div class="abs step" style="top:219px">Quiz
  <svg style="position:absolute;right:16px;top:14px" width="14" height="14" viewBox="0 0 14 14"><circle cx="7" cy="7" r="7" fill="#1d8c8c"/><path d="M4 7.2l2 2 4-4" stroke="#fff" stroke-width="1.5" fill="none"/></svg>
</div>
<div class="abs step current" style="top:271px">Endorsement</div>
<div class="abs step off" style="top:322px">Submission</div>

<h2 class="abs h2">Endorsement</h2>
<div class="abs btn" style="left:1006px;top:213px;width:104px">Save Progress</div>
<div class="abs rule" style="left:365px;top:255px;width:745px"></div>

<div class="abs input" style="left:365px;width:533px">All categories
  <svg style="position:absolute;right:12px;top:8px" width="15" height="15" viewBox="0 0 16 16" fill="none" stroke="#666" stroke-width="1.5"><circle cx="7" cy="7" r="5.5"/><path d="M11 11l4 4"/></svg>
</div>
<div class="abs btn fill" style="left:905px;top:272px;width:64px">Search</div>
<div class="abs btn" style="left:1009px;top:272px;width:101px">Send Request</div>

<div class="abs row" style="top:312px"><div class="abs chk"></div><div class="abs avatar" role="img" aria-label="Colleague photo"></div><div class="abs name">Yara Lind</div><div class="abs role">Art Director</div><div class="abs btn">Add</div></div>
<div class="abs row" style="top:374px"><div class="abs chk"></div><div class="abs avatar" role="img" aria-label="Colleague photo"></div><div class="abs name">Hugo Petit</div><div class="abs role">UI Designer</div><div class="abs btn">Add</div></div>
<div class="abs row" style="top:437px"><div class="abs chk on"><svg width="14" height="14" viewBox="0 0 14 14"><path d="M3 7l3 3 5-6" stroke="#fff" stroke-width="1.8" fill="none"/></svg></div><div class="abs avatar" role="img" aria-label="Colleague photo"></div><div class="abs name">Marco Diaz</div><div class="abs role">Frontend Developer</div><div class="abs btn">Add</div></div>
<div class="abs row" style="top:499px"><div class="abs chk"></div><div class="abs avatar" role="img" aria-label="Colleague photo" style="background:linear-gradient(135deg,#f1d3b0,#c9925e)"></div><div class="abs name">Nora Vance</div><div class="abs role">Cybersecurity Analyst</div><div class="abs btn">Add</div></div>
<div class="abs row" style="top:562px"><div class="abs chk on"><svg width="14" height="14" viewBox="0 0 14 14"><path d="M3 7l3 3 5-6" stroke="#fff" stroke-width="1.8" fill="none"/></svg></div><div class="abs avatar" role="img" aria-label="Colleague photo"></div><div class="abs name">Daniel Moss</div><div class="abs role">DevOps Engineer</div><div class="abs btn">Add</div></div>

<div class="abs pager-btn" style="left:787px;width:62px">‹ Back</div>
<div class="abs page on" style="left:864px">1</div>
<div class="abs page" style="left:898px">2</div>
<div class="abs page" style="left:932px">3</div>
<div class="abs page" style="left:966px">4</div>
<div class="abs page" style="left:1000px">5</div>
<div class="abs pager-btn" style="left:1047px;width:63px">Next ›</div>

<div class="abs pct">65<span>%</span></div>
<div class="abs bar"><i></i></div>
<div class="abs btn" style="left:88px;top:722px;width:72px">Go Back</div>
<div class="abs" style="left:998px;top:730px;font-size:11.5px;color:var(--muted)">Skip ›</div>
<div class="abs btn fill" style="left:1058px;top:722px;width:52px">Next</div>

<div class="abs scrim"></div>

<section class="abs modal" role="dialog" aria-label="Endorsements">
  <h3>Endorsements</h3>
  <div class="rule"></div>
  <div class="avatar" role="img" aria-label="Selected colleague photo" style="left:28px"></div>
  <div class="avatar" role="img" aria-label="Selected colleague photo" style="left:62px"></div>
  <p>You will add <b>2</b> colleagues to endorsement you.</p>
  <label>Effective Date</label>
  <div class="select">Select date
    <svg style="position:absolute;right:14px;top:11px" width="10" height="7" viewBox="0 0 10 7" fill="none" stroke="#333" stroke-width="1.4"><path d="M1 1l4 4 4-4"/></svg>
  </div>
  <div class="btn" style="position:absolute;left:28px;top:220px;width:64px">Cancel</div>
  <div class="btn fill" style="position:absolute;left:220px;top:220px;width:65px">Submit</div>
</section>
</body>
</html>
```